BRIGHTHOLD PROPERTY MANAGEMENT INC. WEBSITE

Please make the website more family-friendly.

I want a website to help me build my property management business by adding listing properties and creating an online application. Im open to any other ideas.
I want a WordPress designer to code it.

Here is my current website. www.brighthold.biz

IDEA: I like the website design https://www.pelicanclimateservices.com/

Thank you

Tom

Number of Pages Required

5+ page

```html
<!DOCTYPE html>
<html lang="en">
<head>
<meta charset="utf-8">
<title>Brighthold Property Management</title>
<link href="https://fonts.googleapis.com/css2?family=EB+Garamond:wght@500;600;700&family=Lato:wght@400;500;700&display=swap" rel="stylesheet">
<style>
:root{
  --red:#9e1015;
  --red-soft:#f3e6e7;
  --ink:#1c1c1c;
  --muted:#444;
  --white:#ffffff;
  --footer:#efefef;
  --rule:#c9c9c9;
  --serif:"EB Garamond", Georgia, serif;
  --sans:"Lato", Arial, sans-serif;
}
*{margin:0;padding:0;box-sizing:border-box}
html,body{width:1200px;height:2332px;overflow:hidden;background:var(--white)}
body{position:relative;font-family:var(--sans);color:var(--ink)}
.abs{position:absolute}

/* header */
.brand{left:111px;top:78px;font-family:var(--serif);font-weight:600;font-size:25px;letter-spacing:1.5px;color:var(--red)}
.contact-item{display:flex;align-items:center;gap:10px;top:12px}
.contact-icon{width:24px;height:24px;border-radius:50%;background:var(--red);display:flex;align-items:center;justify-content:center}
.contact-label{font-family:var(--serif);font-size:11px;color:var(--ink);line-height:1.3}
.contact-value{font-family:var(--serif);font-size:14px;color:var(--muted)}
.vsep{width:1px;height:18px;background:var(--rule);top:23px}
.social{top:19px;width:24px;height:24px;border-radius:50%;background:var(--red)}
.header-rule{left:492px;top:63px;width:614px;height:1px;background:#d8d8d8}
.nav{top:89px;font-family:var(--serif);font-weight:600;font-size:12.5px;letter-spacing:.4px;color:var(--ink)}
.nav-cta{left:1001px;top:81px;width:105px;height:31px;background:var(--red);color:var(--white);font-family:var(--serif);font-weight:700;font-size:12px;display:flex;align-items:center;justify-content:center;letter-spacing:.3px}

/* hero */
.hero-photo{left:0;top:129px;width:1200px;height:660px;
  background:radial-gradient(ellipse at 55% 70%,#6b5236 0%,#3a2c1e 30%,#140f0b 62%,#050505 90%)}
.hero-title{left:0;top:313px;width:1200px;text-align:center;font-family:var(--serif);font-weight:700;font-size:50px;color:var(--white);letter-spacing:.5px}
.hero-btn{left:512px;top:409px;width:176px;height:54px;background:var(--white);display:flex;align-items:center;justify-content:center;font-family:var(--serif);font-weight:600;font-size:21px;color:var(--ink)}
.hero-edge{left:0;top:0}

/* intro */
.section-title{left:0;top:842px;width:1200px;text-align:center;font-family:var(--serif);font-weight:700;font-size:31px;line-height:52px;color:var(--red);letter-spacing:.5px}
.intro-text{left:111px;top:981px;width:433px;font-size:14.8px;line-height:25.8px;color:var(--ink);text-align:justify}
.intro-text p+p{margin-top:25.8px}
.read-more{left:111px;top:1284px;width:130px;height:47px;background:var(--red);color:var(--white);font-family:var(--serif);font-weight:500;font-size:15.5px;display:flex;align-items:center;justify-content:center}
.intro-photo{left:600px;top:988px;width:489px;height:343px;
  background:linear-gradient(135deg,#2b2f9e 0%,#1d1f7a 45%,#3a3fc0 70%,#7b6a9a 100%)}

/* rates */
.rates{left:111px;top:1420px;width:978px;height:427px;background:var(--white);box-shadow:0 6px 28px rgba(0,0,0,.12)}
.rates-head{height:69px;background:var(--red);color:var(--white);font-family:var(--serif);font-weight:700;font-size:21px;display:flex;align-items:center;justify-content:center;letter-spacing:.3px}
.rates-cols{height:68px;background:var(--red-soft);position:relative;font-family:var(--serif);font-weight:600;font-size:20px}
.rates-cols span{position:absolute;top:22px;transform:translateX(-50%)}
.rate-row{position:absolute;font-size:21.5px;font-weight:500;color:var(--ink)}
.rate-name{left:156px}
.rate-value{left:691px;width:58px;text-align:center}

/* footer */
.footer{left:0;top:1929px;width:1200px;height:403px;background:var(--footer)}
.footer-brand{left:106px;top:2131px;font-family:var(--serif);font-weight:600;font-size:38px;letter-spacing:2px;color:var(--red)}
.footer-heading{top:2003px;font-size:21px;font-weight:500;color:var(--ink)}
.footer-list{list-style:none;top:2046px}
.footer-list li{display:flex;align-items:center;gap:10px;font-size:15px;height:34.4px;color:var(--ink)}
.contact-row{left:846px;display:flex;gap:12px;font-size:15px;line-height:26px}
.contact-row .dot{width:32px;height:32px;border-radius:50%;background:var(--red);flex:none;display:flex;align-items:center;justify-content:center}
.footer-rule{left:111px;top:2252px;width:978px;height:1px;background:var(--rule)}
.copyright{left:0;top:2287px;width:1200px;text-align:center;font-size:15.5px;color:var(--ink)}
</style>
</head>
<body>

<header>
  <div class="abs brand">BRIGHTHOLD</div>

  <div class="abs contact-item" style="left:493px">
    <div class="contact-icon"><svg width="12" height="12" viewBox="0 0 24 24"><path fill="#fff" d="M6.6 10.8a15 15 0 0 0 6.6 6.6l2.2-2.2c.3-.3.7-.4 1-.2 1.1.4 2.3.6 3.6.6.6 0 1 .4 1 1V20c0 .6-.4 1-1 1A17 17 0 0 1 3 4c0-.6.4-1 1-1h3.5c.6 0 1 .4 1 1 0 1.3.2 2.5.6 3.6.1.3 0 .7-.2 1z"/></svg></div>
    <div><div class="contact-label">Phone:</div><div class="contact-value">+1 555 014 2290</div></div>
  </div>
  <div class="abs vsep" style="left:679px"></div>
  <div class="abs contact-item" style="left:729px">
    <div class="contact-icon"><svg width="13" height="10" viewBox="0 0 26 20"><rect x="1" y="1" width="24" height="18" rx="2" fill="none" stroke="#fff" stroke-width="2.5"/><path d="M2 3l11 8 11-8" fill="none" stroke="#fff" stroke-width="2.5"/></svg></div>
    <div><div class="contact-label">Email:</div><div class="contact-value">info@brighthold.biz</div></div>
  </div>
  <div class="abs vsep" style="left:940px"></div>
  <div class="abs social" style="left:985px"></div>
  <div class="abs social" style="left:1016px"></div>
  <div class="abs social" style="left:1048px"></div>
  <div class="abs social" style="left:1080px"></div>

  <div class="abs header-rule"></div>
  <nav>
    <span class="abs nav" style="left:491px">LISTINGS OWNERS</span>
    <span class="abs nav" style="left:641px">PROSPECT</span>
    <span class="abs nav" style="left:745px">TENANTS</span>
    <span class="abs nav" style="left:843px">ABOUT</span>
    <span class="abs nav" style="left:927px">MORE</span>
    <span class="abs nav-cta">CONTACT US</span>
  </nav>
</header>

<section class="hero">
  <div class="abs hero-photo" role="img" aria-label="Model house beside stacked coins forming a rising bar chart on a dark background"></div>
  <svg class="abs hero-edge" width="1200" height="800" viewBox="0 0 1200 800">
    <polygon points="0,578 600,757 1200,578 1200,800 0,800" fill="#fff"/>
    <polygon points="0,588 600,770 988,652 600,790 0,620" fill="#9e1015"/>
  </svg>
  <h1 class="abs hero-title">WELCOME TO BRIGHTHOLD</h1>
  <div class="abs hero-btn">GET STARTED</div>
</section>

<section class="intro">
  <h2 class="abs section-title">PROPERTY MANAGEMENT ELK GROVE, SACRAMENTO<br>&amp; SURROUNDING AREAS</h2>
  <div class="abs intro-text">
    <p>Having the right property manager means having an agent who is committed to helping you and making being a home provider hassle free. I believe clear communication, work ethic, time management, staying focused and knowledge goes a long way in my business.This commitment level has helped us build a remarkable track record of delivering results and maintaining a long lasting business partnership with our clients.</p>
    <p>Additionally whether you are an experienced investor or a first time home seller or buyer, we can help you in finding the property of your dreams.</p>
  </div>
  <div class="abs read-more">READ MORE</div>
  <div class="abs intro-photo" role="img" aria-label="Hands using a laptop with glowing digital property documents floating above the keyboard"></div>
</section>

<section class="abs rates">
  <div class="rates-head">MORTGAGE RATES</div>
  <div class="rates-cols"><span style="left:256px">NATIONAL</span><span style="left:719px">AVERAGE RATE</span></div>
  <div class="rate-row rate-name" style="top:172px">30-YEAR FHA RATE</div><div class="rate-row rate-value" style="top:172px">7.07%</div>
  <div class="rate-row rate-name" style="top:234px">30-YEAR FIXED RATE</div><div class="rate-row rate-value" style="top:234px">7.31%</div>
  <div class="rate-row rate-name" style="top:296px">20-YEAR FIXED RATE</div><div class="rate-row rate-value" style="top:296px">7.19%</div>
  <div class="rate-row rate-name" style="top:358px">15-YEAR FIXED RATE</div><div class="rate-row rate-value" style="top:358px">6.52%</div>
</section>

<footer>
  <div class="abs footer"></div>
  <div class="abs footer-brand">BRIGHTHOLD</div>

  <div class="abs footer-heading" style="left:421px">QUICK LINKS</div>
  <ul class="abs footer-list" style="left:421px">
    <li><svg width="14" height="12" viewBox="0 0 14 12"><path d="M0 6h11M7 1l5 5-5 5" fill="none" stroke="#1c1c1c" stroke-width="2.2"/></svg>Home</li>
    <li><svg width="14" height="12" viewBox="0 0 14 12"><path d="M0 6h11M7 1l5 5-5 5" fill="none" stroke="#1c1c1c" stroke-width="2.2"/></svg>About</li>
    <li><svg width="14" height="12" viewBox="0 0 14 12"><path d="M0 6h11M7 1l5 5-5 5" fill="none" stroke="#1c1c1c" stroke-width="2.2"/></svg>Services</li>
    <li><svg width="14" height="12" viewBox="0 0 14 12"><path d="M0 6h11M7 1l5 5-5 5" fill="none" stroke="#1c1c1c" stroke-width="2.2"/></svg>Listing</li>
    <li><svg width="14" height="12" viewBox="0 0 14 12"><path d="M0 6h11M7 1l5 5-5 5" fill="none" stroke="#1c1c1c" stroke-width="2.2"/></svg>Contact Us</li>
  </ul>

  <div class="abs footer-heading" style="left:640px">HELP LINKS</div>
  <ul class="abs footer-list" style="left:640px">
    <li><svg width="14" height="12" viewBox="0 0 14 12"><path d="M0 6h11M7 1l5 5-5 5" fill="none" stroke="#1c1c1c" stroke-width="2.2"/></svg>FAQ</li>
    <li><svg width="14" height="12" viewBox="0 0 14 12"><path d="M0 6h11M7 1l5 5-5 5" fill="none" stroke="#1c1c1c" stroke-width="2.2"/></svg>Terms of use</li>
    <li><svg width="14" height="12" viewBox="0 0 14 12"><path d="M0 6h11M7 1l5 5-5 5" fill="none" stroke="#1c1c1c" stroke-width="2.2"/></svg>Privacy Policy</li>
    <li><svg width="14" height="12" viewBox="0 0 14 12"><path d="M0 6h11M7 1l5 5-5 5" fill="none" stroke="#1c1c1c" stroke-width="2.2"/></svg>Support Links</li>
    <li><svg width="14" height="12" viewBox="0 0 14 12"><path d="M0 6h11M7 1l5 5-5 5" fill="none" stroke="#1c1c1c" stroke-width="2.2"/></svg>Conditions</li>
  </ul>

  <div class="abs footer-heading" style="left:846px">CONTACT US</div>
  <div class="abs contact-row" style="top:2049px">
    <span class="dot"><svg width="12" height="16" viewBox="0 0 12 16"><path d="M6 0a6 6 0 0 0-6 6c0 4.5 6 10 6 10s6-5.5 6-10a6 6 0 0 0-6-6zm0 8.5A2.5 2.5 0 1 1 6 3.5a2.5 2.5 0 0 1 0 5z" fill="#fff"/></svg></span>
    <span>Brighthold Homes<br>United States</span>
  </div>
  <div class="abs contact-row" style="top:2115px;align-items:center">
    <span class="dot"><svg width="13" height="13" viewBox="0 0 24 24"><path fill="#fff" d="M6.6 10.8a15 15 0 0 0 6.6 6.6l2.2-2.2c.3-.3.7-.4 1-.2 1.1.4 2.3.6 3.6.6.6 0 1 .4 1 1V20c0 .6-.4 1-1 1A17 17 0 0 1 3 4c0-.6.4-1 1-1h3.5c.6 0 1 .4 1 1 0 1.3.2 2.5.6 3.6.1.3 0 .7-.2 1z"/></svg></span>
    <span>+1 555 014 2290</span>
  </div>
  <div class="abs contact-row" style="top:2167px;align-items:center">
    <span class="dot"><svg width="14" height="11" viewBox="0 0 26 20"><rect x="0" y="0" width="26" height="20" rx="2" fill="#fff"/><path d="M1 2l12 8 12-8" fill="none" stroke="#9e1015" stroke-width="2.5"/></svg></span>
    <span>hello@brighthold.biz</span>
  </div>

  <div class="abs footer-rule"></div>
  <div class="abs copyright">Copyrights@2024.Brighthold.All Rights Reserved</div>
</footer>

</body>
</html>
```